I am looking for a modern, clean and neat design for a reflexology and well being business. The business name is Gralo Tund (this is an old Latin word for wellbeing). The colours I would like are purple, white and grey. I am open to suggestions for pictures such as healing or working hands, a pair of feet, images that represent my business that you may think of....... or maybe you think no images at all would be best? My tag line is: "Relax, Renew, Revive" or "Find you balance......... Relax, Renew, Revive" I can decide which I want so I would like to see what both would look like. I would like space on the back to write the client's appointment date and time (more than once)

```html
<!DOCTYPE html>
<html lang="en">
<head>
<meta charset="utf-8">
<title>Gralo Tund – Business Card</title>
<link rel="stylesheet" href="https://fonts.googleapis.com/css2?family=Open+Sans:wght@400;600;700&display=swap">
<style>
  :root {
    --backdrop: #2b2b2d;
    --card-black: #050505;
    --white: #ffffff;
    --lavender: #a7b9e0;
    --mark-grey: #4a4a4a;
    --text-grey: #5a5a5a;
    --faint-grey: #1f1f1f;
    --rule-grey: #cfcfcf;
  }
  * { box-sizing: border-box; margin: 0; padding: 0; }
  html, body { width: 1200px; height: 900px; overflow: hidden; }
  body {
    background: var(--backdrop);
    font-family: "Open Sans", Arial, sans-serif;
    position: relative;
  }
  .card {
    position: absolute;
    left: 290px;
    width: 620px;
    height: 354px;
    background: var(--card-black);
    border-radius: 22px;
    overflow: hidden;
    box-shadow: 0 14px 30px rgba(0,0,0,.5);
    color: var(--white);
  }
  .card--back { top: 60px; }
  .card--front { top: 486px; }

  /* Back */
  .tagline {
    position: absolute; right: 46px; top: 42px;
    font-size: 13px; font-weight: 600; letter-spacing: .5px;
  }
  .brand-block {
    position: absolute; right: 46px; top: 76px;
    display: flex; align-items: center; gap: 10px;
  }
  .brand-dot { width: 22px; height: 22px; border-radius: 50%; background: var(--white); }
  .brand-name { font-size: 22px; font-weight: 600; color: var(--white); }
  .appointment { position: absolute; left: 46px; top: 150px; width: 470px; }
  .appointment__title { font-size: 20px; font-weight: 700; margin-bottom: 14px; }
  .appointment__row {
    display: flex; align-items: flex-end; gap: 4px;
    font-size: 14px; height: 34px;
  }
  .appointment__line { flex: 1; border-bottom: 2px dotted var(--rule-grey); margin-bottom: 5px; }

  /* Front */
  .logo-disc {
    position: absolute; left: -70px; top: 140px;
    width: 420px; height: 420px; border-radius: 50%;
    background: var(--white);
  }
  .logo-lockup {
    position: absolute; left: 40px; top: 222px;
    display: flex; align-items: center; gap: 12px;
  }
  .logo-lockup .brand-dot { width: 30px; height: 30px; background: var(--lavender); }
  .logo-lockup .brand-name { color: var(--text-grey); font-size: 30px; font-weight: 400; letter-spacing: 1px; }
  .faint-brand {
    position: absolute; right: 44px; top: 40px;
    font-size: 26px; color: var(--faint-grey); letter-spacing: 1px;
  }
  .identity { position: absolute; right: 40px; top: 150px; width: 300px; text-align: right; }
  .identity__name { font-size: 24px; font-weight: 700; letter-spacing: 1px; line-height: 1.1; }
  .identity__role { font-size: 13px; color: var(--lavender); font-weight: 600; letter-spacing: 1px; }
  .identity__rule { height: 1px; background: var(--rule-grey); margin-top: 6px; }
  .contacts { position: absolute; left: 350px; top: 232px; list-style: none; }
  .contacts li {
    display: flex; align-items: center; gap: 8px;
    font-size: 14px; line-height: 24px;
  }
  .contacts svg { width: 12px; height: 12px; fill: none; stroke: var(--lavender); stroke-width: 1.6; }
</style>
</head>
<body>

<section class="card card--back">
  <p class="tagline">RELAX, RENEW, REVIVE</p>
  <div class="brand-block">
    <span class="brand-dot"></span>
    <span class="brand-name">Gralo Tund</span>
  </div>
  <div class="appointment">
    <h2 class="appointment__title">Appointment:</h2>
    <div class="appointment__row"><span>Name:</span><span class="appointment__line"></span></div>
    <div class="appointment__row"><span>Time:</span><span class="appointment__line"></span></div>
    <div class="appointment__row"><span>Date:</span><span class="appointment__line"></span></div>
  </div>
</section>

<section class="card card--front">
  <p class="faint-brand">GRALO TUND</p>
  <div class="logo-disc"></div>
  <div class="logo-lockup">
    <span class="brand-dot"></span>
    <span class="brand-name">GRALO TUND</span>
  </div>
  <div class="identity">
    <p class="identity__name">MARA QUILLON</p>
    <p class="identity__role">DIRECTOR</p>
    <div class="identity__rule"></div>
  </div>
  <ul class="contacts">
    <li>
      <svg viewBox="0 0 12 12"><path d="M2 1.5l2 .5 .8 2.2-1.2 1a6 6 0 0 0 3.2 3.2l1-1.2 2.2.8.5 2c-4.5.5-9-4-8.5-8.5z"/></svg>
      +330 2715-0392
    </li>
    <li>
      <svg viewBox="0 0 12 12"><rect x="1" y="2.5" width="10" height="7"/><path d="M1 2.5l5 4 5-4"/></svg>
      info@gralotund.com
    </li>
    <li>
      <svg viewBox="0 0 12 12"><circle cx="6" cy="6" r="5"/><path d="M1 6h10M6 1c-2.5 3-2.5 7 0 10M6 1c2.5 3 2.5 7 0 10"/></svg>
      www.gralotund.com
    </li>
  </ul>
</section>

</body>
</html>
```